Harborline Benches business cards

I’d like a business card design that includes my logo, a tag line and my contact info. Black, textured background. My contact info color should match the orange and blue gradients. Tagline under logo: “Wooden Tables and Furniture of the Highest Quality”

Target Market(s)

High end furniture buyers

Contact Information for Business Card

Contact info, logo and tagline

```html
<!DOCTYPE html>
<html lang="en">
<head>
<meta charset="utf-8">
<title>Harborline Benches — Business Cards</title>
<link rel="stylesheet" href="https://fonts.googleapis.com/css2?family=Poppins:wght@400;500;600&display=swap">
<style>
  :root {
    --stage: #2b2b2b;
    --card-white: #ffffff;
    --ink: #1f1f1f;
    --orange: #ee7526;
    --blue: #0d50a4;
    --grad-orange: #ef7424;
    --grad-mid: #86676a;
    --grad-blue: #1f5aa0;
  }
  * { margin: 0; padding: 0; box-sizing: border-box; }
  html, body {
    width: 1093px; height: 1200px; overflow: hidden;
    background: var(--stage);
    font-family: "Poppins", sans-serif;
  }
  .canvas { position: relative; width: 1093px; height: 1200px; }
  .card {
    position: absolute; left: 264px;
    border-radius: 24px; overflow: hidden;
  }
  .card--front { top: 226px; width: 578px; height: 356px; background: var(--card-white); color: var(--ink); }
  .card--back {
    top: 621px; width: 582px; height: 356px; color: #fff;
    background: linear-gradient(to top right, var(--grad-orange) 0%, #c8703f 30%, var(--grad-mid) 62%, var(--grad-blue) 100%);
  }
  .brand {
    position: absolute; font-weight: 600; letter-spacing: 0.2px; white-space: nowrap;
    display: flex; align-items: center; gap: 8px;
  }
  .brand__dot { width: 12px; height: 12px; border-radius: 50%; }
  .card--front .brand { right: 32px; top: 76px; font-size: 28px; color: var(--blue); line-height: 1; }
  .card--front .brand__dot { background: var(--orange); }
  .card--back .brand { left: 0; right: 0; justify-content: center; top: 176px; font-size: 36px; color: #fff; line-height: 1; }
  .card--back .brand__dot { background: #fff; }

  .person { position: absolute; left: 37px; top: 170px; }
  .person__name { font-size: 30px; font-weight: 600; line-height: 1; }
  .person__first { color: var(--orange); }
  .person__last { color: var(--blue); }
  .person__role { font-size: 17px; line-height: 1; margin-top: 7px; }
  .rule { position: absolute; left: 206px; right: 32px; top: 217px; height: 1px; background: var(--orange); }

  .contacts { position: absolute; left: 37px; top: 259px; list-style: none; font-size: 17px; line-height: 21px; }
  .contacts li { display: flex; align-items: center; gap: 8px; }
  .contacts svg { width: 15px; height: 15px; flex: none; }
  .accent { color: var(--orange); }
  .address { position: absolute; right: 32px; top: 280px; text-align: right; font-size: 17px; line-height: 21px; }

  .tagline { position: absolute; left: 0; right: 0; top: 296px; text-align: center; font-size: 17px; }
</style>
</head>
<body>
<main class="canvas">
  <section class="card card--front" aria-label="Business card front">
    <div class="brand"><span class="brand__dot"></span>Harborline Benches</div>
    <div class="person">
      <p class="person__name"><span class="person__first">Marcus</span> <span class="person__last">Ellery</span></p>
      <p class="person__role">Managing Director</p>
    </div>
    <div class="rule"></div>
    <ul class="contacts">
      <li>
        <svg viewBox="0 0 24 24" fill="none" stroke="#ee7526" stroke-width="2.4" stroke-linecap="round" stroke-linejoin="round" aria-hidden="true"><path d="M5 3h4l2 5-2.5 1.5a11 11 0 0 0 6 6L16 13l5 2v4a2 2 0 0 1-2 2A17 17 0 0 1 3 5a2 2 0 0 1 2-2z"/><path d="M15 3a6 6 0 0 1 6 6M15 7a2 2 0 0 1 2 2"/></svg>
        <span>044-555 210 346</span>
      </li>
      <li>
        <svg viewBox="0 0 24 24" aria-hidden="true"><rect x="1" y="5" width="22" height="14" fill="#ee7526"/><path d="M1 5l11 8 11-8M1 19l8-7M23 19l-8-7" fill="none" stroke="#fff" stroke-width="1.6"/></svg>
        <span>info@harborline.com</span>
      </li>
      <li>
        <svg viewBox="0 0 24 24" fill="none" stroke="#ee7526" stroke-width="1.8" aria-hidden="true"><circle cx="12" cy="12" r="10"/><ellipse cx="12" cy="12" rx="4.5" ry="10"/><path d="M2 12h20M4 7h16M4 17h16"/></svg>
        <span>www.<span class="accent">harborline</span>.com</span>
      </li>
    </ul>
    <address class="address" style="font-style:normal">421, Address line goes here<br>45452,Country Name</address>
  </section>

  <section class="card card--back" aria-label="Business card back">
    <div class="brand"><span class="brand__dot"></span>Harborline Benches</div>
    <p class="tagline">Wooden Tables and Furniture of the Highest Quality</p>
  </section>
</main>
</body>
</html>
```